Varnex Consulting Business card design.

See our website www.varnexconsulting.example which will give you a good idea of what we are about. The font is called 'Play'.

I'd like a standout business card in keeping with the themes and branding on the website

Target Market(s)

professionals. HR directors

Industry/Entity Type

Business

Contact Information for Business Card

Varnex Consulting PO Box 3172 Merrowdale NSW 2291 1300 485 193 Gavin Threlkeld Principal email: career@varnexconsulting.example ABN: 71203948865

Font styles to use
Other font styles liked:
• Play

Requirements
Must have
• Must have same design colours and branding as website.
• On back I'd prefer a list of the things we do which appears below the name at the header on the website

```html
<!DOCTYPE html>
<html lang="en">
<head>
<meta charset="utf-8">
<title>Varnex Consulting – Business Card</title>
<link href="https://fonts.googleapis.com/css2?family=Play:wght@400;700&display=swap" rel="stylesheet">
<style>
  :root {
    --page-bg: #a8a5a5;
    --card-navy: #132a3e;
    --brand-blue: #2a8fdc;
    --text-light: #eef1f4;
  }
  * { margin: 0; padding: 0; box-sizing: border-box; }
  html, body {
    width: 1200px;
    height: 1200px;
    overflow: hidden;
    background: var(--page-bg);
    font-family: 'Play', sans-serif;
  }
  .canvas {
    position: relative;
    width: 1200px;
    height: 1200px;
  }
  .card {
    position: absolute;
    left: 200px;
    width: 800px;
    height: 470px;
    background: var(--card-navy);
    color: var(--text-light);
    text-align: center;
  }
  .card--front { top: 110px; }
  .card--back  { top: 640px; }

  .company-name {
    position: absolute;
    left: 0; right: 0;
    display: flex;
    justify-content: center;
    align-items: center;
    gap: 18px;
    font-weight: 400;
    font-size: 56px;
    line-height: 1;
    color: var(--text-light);
  }
  .company-name .mark {
    display: block;
    width: 16px;
    height: 16px;
    background: var(--brand-blue);
  }
  .services {
    position: absolute;
    left: 0; right: 0;
    font-size: 17px;
    letter-spacing: 2.4px;
    color: var(--brand-blue);
    line-height: 1;
  }
  .services .sep { margin: 0 8px; letter-spacing: 0; }

  .card--front .company-name { top: 150px; }
  .card--front .services { top: 226px; }

  .website {
    position: absolute;
    left: 0; right: 0;
    top: 393px;
    display: flex;
    justify-content: center;
    align-items: center;
    gap: 12px;
    font-size: 20px;
    line-height: 1;
  }
  .website .domain { color: var(--brand-blue); }
  .website svg { display: block; }

  .card--back .company-name { top: 62px; font-size: 52px; }
  .card--back .services { top: 134px; font-size: 16px; }

  .person-name {
    position: absolute;
    left: 0; right: 0;
    top: 200px;
    font-weight: 700;
    font-size: 29px;
    color: var(--brand-blue);
    line-height: 1;
  }
  .person-role {
    position: absolute;
    left: 0; right: 0;
    top: 240px;
    font-size: 19px;
    line-height: 1;
  }
  .contact {
    position: absolute;
    left: 0; right: 0;
    top: 312px;
    font-size: 20px;
    line-height: 26.5px;
    font-style: normal;
  }
  .abn {
    position: absolute;
    left: 0; right: 0;
    top: 400px;
    font-size: 20px;
    line-height: 1;
  }
  .abn .label { color: var(--brand-blue); }
</style>
</head>
<body>
<main class="canvas">

  <section class="card card--front" aria-label="Card front">
    <h1 class="company-name"><span class="mark" aria-hidden="true"></span>Varnex Consulting</h1>
    <p class="services">Search &amp; Select<span class="sep">|</span>Career<span class="sep">|</span>Coaching<span class="sep">|</span>Leadership<span class="sep">|</span>Outplacement</p>
    <p class="website">
      <svg width="38" height="4" viewBox="0 0 38 4" aria-hidden="true"><polygon points="0,2 38,0.4 38,3.6" fill="var(--brand-blue)"/></svg>
      <span>www.<span class="domain">varnexconsulting</span>.example</span>
      <svg width="38" height="4" viewBox="0 0 38 4" aria-hidden="true"><polygon points="38,2 0,0.4 0,3.6" fill="var(--brand-blue)"/></svg>
    </p>
  </section>

  <section class="card card--back" aria-label="Card back">
    <h2 class="company-name"><span class="mark" aria-hidden="true"></span>Varnex Consulting</h2>
    <p class="services">Search &amp; Select<span class="sep">|</span>Career<span class="sep">|</span>Coaching<span class="sep">|</span>Leadership<span class="sep">|</span>Outplacement</p>
    <p class="person-name">Gavin Threlkeld</p>
    <p class="person-role">Principal</p>
    <address class="contact">
      1300 485 193<br>
      career@varnexconsulting.example<br>
      PO Box 3172 Merrowdale NSW 2291
    </address>
    <p class="abn"><span class="label">ABN:</span> 71203948865</p>
  </section>

</main>
</body>
</html>
```